Termite Mailer September 2021

We need a clean modern looking flyer advertising termites via the mail.

Size should be 9"x6"

Our tagline is "The Smarter Approach to Pest Control"

Something along the stylistic design of these:

https://pics.lumora-share.net/Qk82vLmTzPwX4rNa1

https://pics.lumora-share.net/Hd37nBcYxTqW9sKe5

https://pics.lumora-share.net/Zr61pMfVaLuE2jGo8

https://www.cardvistaprint.net/wp-content/uploads/designs/img/Pest-Prevention-Postcard-PST-1003.jpg

Should include some of this verbiage:

HAVE YOU SCHEDULED YOUR ANNUAL TERMITE INSPECTION? - MAKE IT IN RED

DON'T WAIT. PROTECT YOUR HOME TODAY!

ABSOLUTELY FREE INSPECTION. NO OBLIGATION.

TERMITES CAN CAUSE SEVERE DAMAGE TO YOUR HOME.

BRIMVALE LOGO

THE SMARTER APPROACH TO PEST CONTROL.

PROTECT YOUR MOST VALUABLE ASSET.

10% DISCOUNT ON ANY SERVICE GUARANTEED IF YOU CALL TODAY.

INCLUDE A PICTURE OF A TERMITE AS WELL SOMEWHERE AND WOOD DAMAGE.

Target Market(s)

Homeowners in Southern California USA

Industry/Entity Type

Pest Control/Extermination

Font styles to use
Other font styles liked:
• Chaparral Pro Italic, Brava Slab

Requirements
Must have
• Clean design, picture of house, picture of Termite, 10% off coupon and call to action on the back
Should not have
• Bad looking houses, colors that don't match our logo

```html
<!DOCTYPE html>
<html lang="en">
<head>
<meta charset="utf-8">
<title>Brimvale Termite Mailer</title>
<link href="https://fonts.googleapis.com/css2?family=Alegreya:ital,wght@0,700;0,800;0,900;1,400&display=swap" rel="stylesheet">
<style>
  :root {
    --brand-blue: #0b72b9;
    --brand-green: #7cc242;
    --alert-red: #d21f3c;
    --paper: #ffffff;
    --rule-grey: #d5d5d5;
    --wood-dark: #6e2f17;
    --wood-light: #b5623a;
    --sky: #dfe6ea;
    --roof: #9c7a5a;
    --suit-light: #eef3f8;
    --suit-shade: #c4d2df;
  }
  * { margin: 0; padding: 0; box-sizing: border-box; }
  html, body { width: 1200px; height: 802px; overflow: hidden; background: var(--paper); }
  .mailer {
    position: relative;
    width: 1200px;
    height: 802px;
    font-family: "Alegreya", Georgia, serif;
    font-weight: 800;
    text-transform: uppercase;
  }
  .mailer-art { position: absolute; left: 0; top: 0; width: 1200px; height: 802px; }
  .copy { position: absolute; line-height: 1; white-space: nowrap; }
  .headline-asset { left: 610px; top: 91px; font-size: 25px; color: var(--paper); letter-spacing: 1.3px; }
  .inspection-question { left: 110px; top: 179px; width: 392px; text-align: right; font-size: 19.8px; color: var(--paper); line-height: 1.18; letter-spacing: .4px; }
  .dont-wait { left: 62px; top: 277px; font-size: 37px; color: var(--brand-blue); letter-spacing: 1px; font-weight: 900; }
  .protect-home { left: 62px; top: 318px; font-size: 29.4px; color: var(--brand-green); letter-spacing: 1px; }
  .free-offer { left: 63px; top: 382px; font-size: 26px; color: var(--brand-blue); line-height: 1.27; letter-spacing: 1px; }
  .free-offer .free { color: var(--alert-red); }
  .damage-warning { left: 62px; top: 503px; font-size: 20.4px; color: var(--paper); line-height: 1.27; letter-spacing: .8px; }
  .discount-figure { left: 86px; top: 607px; font-size: 74px; color: var(--paper); font-weight: 900; letter-spacing: -1px; }
  .discount-label { left: 84px; top: 678px; font-size: 24px; color: var(--paper); letter-spacing: 1px; }
  .discount-terms { left: 72px; top: 740px; font-size: 16.5px; color: var(--paper); letter-spacing: .9px; }
  .brand-name { left: 622px; top: 591px; font-size: 44px; color: var(--brand-blue); font-weight: 900; letter-spacing: .5px; }
  .tagline { left: 445px; top: 663px; font-size: 30px; color: var(--brand-blue); font-style: italic; font-weight: 400; text-transform: none; }
</style>
</head>
<body>
<main class="mailer">
  <svg class="mailer-art" viewBox="0 0 2340 1564" preserveAspectRatio="none">
    <defs>
      <radialGradient id="termite-tone" cx="45%" cy="45%" r="60%">
        <stop offset="0" stop-color="#f0d9b0"/>
        <stop offset="0.6" stop-color="#c98a3a"/>
        <stop offset="1" stop-color="#6b3d16"/>
      </radialGradient>
      <linearGradient id="house-tone" x1="0" y1="0" x2="0" y2="1">
        <stop offset="0" stop-color="var(--sky)"/>
        <stop offset="0.35" stop-color="var(--roof)"/>
        <stop offset="0.6" stop-color="#d9cdb4"/>
        <stop offset="1" stop-color="#6f7d4a"/>
      </linearGradient>
      <linearGradient id="wood-tone" x1="0" y1="0" x2="1" y2="1">
        <stop offset="0" stop-color="var(--wood-light)"/>
        <stop offset="1" stop-color="var(--wood-dark)"/>
      </linearGradient>
      <linearGradient id="technician-tone" x1="0" y1="0" x2="1" y2="1">
        <stop offset="0" stop-color="var(--suit-light)"/>
        <stop offset="1" stop-color="var(--suit-shade)"/>
      </linearGradient>
    </defs>

    <rect class="card-base" x="63" y="48" width="2174" height="1452" fill="var(--brand-blue)"/>

    <path class="swoosh-green" d="M1700 430 C1950 490 2150 430 2237 300 L2237 400 C2100 475 1900 500 1700 430 Z" fill="var(--brand-green)"/>

    <path class="photo-frame" d="M1005 470 C1150 330 1450 300 1700 420 C1900 505 2100 475 2237 395 L2237 1015 C2000 1045 1850 1055 1760 1025 C1550 935 1450 820 1300 800 C1200 790 1100 800 1005 765 Z" fill="var(--paper)"/>
    <g role="img" aria-label="Photo of a well-kept single-storey stucco home with landscaped garden">
      <path d="M1013 468 C1150 342 1450 312 1700 430 C1900 512 2100 482 2237 408 L2237 1005 C2000 1035 1850 1045 1762 1015 C1555 925 1450 812 1300 792 C1200 780 1100 792 1013 752 Z" fill="url(#house-tone)"/>
    </g>

    <path class="swoosh-edge" d="M1200 810 C1350 790 1450 830 1580 935" fill="none" stroke="var(--brand-green)" stroke-width="26"/>

    <path class="sweep-white" d="M835 1500 C780 1350 795 1150 950 1065 C1100 985 1400 1000 1580 935 C1650 975 1700 1010 1760 1025 C1900 1050 2100 1030 2237 1012 L2237 1500 Z" fill="var(--paper)"/>

    <rect class="message-panel" x="63" y="461" width="947" height="477" fill="var(--paper)"/>
    <line class="panel-rule" x1="122" y1="715" x2="962" y2="715" stroke="var(--rule-grey)" stroke-width="3"/>

    <rect class="question-banner" x="237" y="333" width="771" height="118" fill="var(--alert-red)"/>

    <g role="img" aria-label="Magnifying glass over a close-up photo of termites">
      <circle cx="352" cy="212" r="142" fill="#d8d8d8"/>
      <circle cx="352" cy="212" r="128" fill="url(#termite-tone)"/>
      <path d="M250 325 L140 460 L205 460 L275 345 Z" fill="#d99a2b"/>
    </g>

    <g role="img" aria-label="White silhouettes of an ant, a bed bug and a mosquito" fill="var(--paper)" opacity="0.9">
      <ellipse cx="590" cy="205" rx="40" ry="72"/>
      <ellipse cx="768" cy="210" rx="46" ry="70"/>
      <ellipse cx="946" cy="205" rx="52" ry="68"/>
    </g>

    <circle cx="1068" cy="928" r="182" fill="var(--paper)"/>
    <circle cx="1068" cy="928" r="180" fill="none" stroke="#d0d0d0" stroke-width="3"/>
    <g role="img" aria-label="Photo of termite-damaged floor joists and wood">
      <circle cx="1068" cy="928" r="162" fill="url(#wood-tone)"/>
    </g>

    <line x1="578" y1="1003" x2="858" y2="1003" stroke="var(--brand-green)" stroke-width="4"/>
    <circle cx="859" cy="1003" r="10" fill="var(--brand-green)"/>

    <path class="discount-tab" d="M115 1500 L115 1265 C115 1175 185 1120 285 1120 C385 1120 455 1175 455 1265 L455 1408 L958 1408 C983 1408 997 1422 997 1445 L997 1500 Z" fill="var(--brand-green)"/>

    <circle class="brand-dot" cx="1160" cy="1198" r="34" fill="var(--brand-green)"/>

    <g role="img" aria-label="Photo of a pest control technician in a white protective suit holding a sprayer">
      <rect x="1700" y="740" width="537" height="760" fill="url(#technician-tone)"/>
    </g>
  </svg>

  <div class="copy headline-asset">Protect your most valuable asset</div>
  <div class="copy inspection-question">Have you scheduled<br>your annual termite inspection?</div>
  <div class="copy dont-wait">Don't wait</div>
  <div class="copy protect-home">Protect your home today !</div>
  <div class="copy free-offer">Absolutely <span class="free">free</span> inspection.<br>No obligation.</div>
  <div class="copy damage-warning">Termites can cause<br>severe damage to your home.</div>
  <div class="copy discount-figure">10%</div>
  <div class="copy discount-label">Discount</div>
  <div class="copy discount-terms">On any service guaranteed if you call today</div>
  <div class="copy brand-name">Brimvale</div>
  <div class="copy tagline">The Smarter Approach to Pest Control</div>
</main>
</body>
</html>
```